BLS Business Card 2018

Larkmere Chiropractic. We have two locations that we want to advertise on the same card. Brightvale OrthoCore campus address: 3815 Pellham Dr., Suite 240, Ashcombe, ST 39417. Brennan address: 246 Willowmere Dr., Building D., Brennan, ST 39284. website: www.drlarkmere-example.com. o:(555)555-0147 f:(555)555-0183

Target Market(s)

Health care decision makers: primary care doctors and mothers

Contact Information for Business Card

I have no idea; up for any suggestions and I'd do much better picking from examples versus describing what I'm looking for. We are in a very high end location and would like the cards to look really sharp.

Requirements
Must have
• My name, Martin R Belvane, D.C.

```html
<!DOCTYPE html>
<html lang="en">
<head>
<meta charset="utf-8">
<title>Larkmere Chiropractic – Business Card</title>
<link rel="stylesheet" href="https://fonts.googleapis.com/css2?family=Cinzel:wght@400;500;600;700&family=Open+Sans:wght@400;600&display=swap">
<style>
  :root {
    --backdrop: #8a4f22;
    --card-light: #dcb68a;
    --card-mid: #c99c6c;
    --card-dark: #b88a5b;
    --ink: #140d06;
    --rule: #24180c;
  }
  * { margin: 0; padding: 0; box-sizing: border-box; }
  html, body {
    width: 1200px; height: 900px; overflow: hidden;
    background: var(--backdrop);
  }
  .canvas { position: relative; width: 1200px; height: 900px; }
  .card {
    position: absolute;
    width: 556px; height: 343px;
    background: radial-gradient(ellipse at 25% 10%, var(--card-light) 0%, var(--card-mid) 55%, var(--card-dark) 100%);
    box-shadow: 3px 4px 8px rgba(0,0,0,0.35);
    color: var(--ink);
  }
  .card--contact { left: 330px; top: 90px; }
  .card--brand { left: 330px; top: 470px; width: 558px; }

  .contact {
    position: absolute; left: 0; right: 0; top: 44px;
    text-align: center;
    font-family: "Open Sans", sans-serif;
    font-size: 16px; line-height: 20px;
  }
  .contact__name {
    font-family: "Cinzel", serif;
    font-weight: 600; font-size: 18px; letter-spacing: 0.03em;
    text-transform: uppercase;
    line-height: 24px;
  }
  .contact__rule {
    width: 214px; height: 1px; background: var(--rule);
    margin: 8px auto 8px;
  }
  .contact__label { font-weight: 600; }
  .contact__place { font-weight: 600; text-transform: uppercase; }

  .brand {
    position: absolute; left: 92px; top: 128px;
    display: flex; align-items: center; gap: 16px;
  }
  .brand__mark {
    width: 76px; height: 76px; border-radius: 50%;
    background: var(--ink);
  }
  .brand__name {
    font-family: "Cinzel", serif; font-weight: 700;
    color: var(--ink); line-height: 1;
  }
  .brand__name-main { display: block; font-size: 40px; letter-spacing: 0.01em; }
  .brand__name-sub { display: block; font-size: 25px; letter-spacing: 0.03em; margin-top: 4px; }
</style>
</head>
<body>
<main class="canvas">
  <section class="card card--contact">
    <div class="contact">
      <p class="contact__name">Martin R Belvane, D.C.</p>
      <div class="contact__rule"></div>
      <p><span class="contact__label">P:</span> (555)555-0147</p>
      <p><span class="contact__label">F:</span> (555)555-0183</p>
      <p>www.drlarkmere-example.com</p>
      <div class="contact__rule"></div>
      <p class="contact__place">Brightvale OrthoCore Campus</p>
      <p>3815 Pellham Drive, Suite 240</p>
      <p>Ashcombe, ST 39417.</p>
      <div class="contact__rule"></div>
      <p class="contact__place">Brennan</p>
      <p>246 Willowmere Dr., Building D.,</p>
      <p>Brennan, ST 39284.</p>
    </div>
  </section>

  <section class="card card--brand">
    <div class="brand">
      <div class="brand__mark"></div>
      <p class="brand__name">
        <span class="brand__name-main">LARKMERE</span>
        <span class="brand__name-sub">CHIROPRACTIC</span>
      </p>
    </div>
  </section>
</main>
</body>
</html>
```